Ridgeline Journeys business card

please see website
www.ridgelinejourneys.comau

info needed on card
Curtis Halvey
Ph
email
Adventure Riding GPS trails

please use my logo and colours off my site

Curtis Halvey
curtis@ridgelinejourneys.com

```html
<!DOCTYPE html>
<html lang="en">
<head>
<meta charset="utf-8">
<title>Ridgeline Journeys – Business Card</title>
<link rel="stylesheet" href="https://fonts.googleapis.com/css2?family=Source+Sans+3:ital,wght@0,400;0,600;0,700;1,600&display=swap">
<style>
  :root {
    --backdrop: #4a4a4a;
    --card-white: #f7f7f7;
    --card-black: #000000;
    --brand-yellow: #f3e01a;
    --ink: #111111;
    --text-light: #f2f2f2;
    --disc: #efefef;
  }
  * { margin: 0; padding: 0; box-sizing: border-box; }
  html, body {
    width: 1200px; height: 750px; overflow: hidden;
    background: var(--backdrop);
    font-family: "Source Sans 3", "Myriad Pro", sans-serif;
  }
  .business-card {
    position: absolute; left: 180px; top: 134px;
    width: 840px; height: 481px;
    background: var(--card-white);
    overflow: hidden;
    box-shadow: 0 6px 14px rgba(0,0,0,.45);
  }
  .brand {
    position: absolute; left: 52px; top: 92px;
    display: flex; align-items: center; gap: 18px;
  }
  .brand-dot {
    width: 46px; height: 46px; border-radius: 50%;
    background: var(--brand-yellow);
  }
  .brand-name {
    font-weight: 700; font-size: 42px; line-height: 1;
    color: var(--ink); letter-spacing: .5px;
  }
  .contact-band {
    position: absolute; left: 0; top: 238px;
    width: 100%; height: 243px;
    background: var(--card-black);
  }
  .band-disc {
    position: absolute; left: 544px; top: 236px;
    width: 242px; height: 242px; border-radius: 50%;
    background: var(--disc);
  }
  .holder-name {
    position: absolute; left: 50px; top: 264px;
    font-weight: 600; font-size: 31px; color: var(--brand-yellow);
  }
  .contact-list {
    position: absolute; left: 50px; top: 318px;
    list-style: none;
  }
  .contact-item {
    display: flex; align-items: center; gap: 12px;
    height: 32px; font-size: 20px; color: var(--text-light);
  }
  .contact-icon { width: 20px; height: 20px; flex: none; }
  .tagline {
    position: absolute; left: 50px; top: 417px;
    font-style: italic; font-weight: 600; font-size: 23px;
    color: var(--text-light);
  }
</style>
</head>
<body>
  <div class="business-card">
    <div class="brand">
      <span class="brand-dot"></span>
      <span class="brand-name">Ridgeline Journeys</span>
    </div>

    <div class="contact-band"></div>
    <div class="band-disc"></div>

    <div class="holder-name">Curtis Halvey</div>

    <ul class="contact-list">
      <li class="contact-item">
        <svg class="contact-icon" viewBox="0 0 20 20" aria-hidden="true">
          <path fill="#f3e01a" d="M4 1.5l3 .5 1.5 4-2 1.5c1 2.3 2.7 4 5 5l1.5-2 4 1.5.5 3c-.5 1.5-2 2.5-3.5 2.5C8 17 3 12 2.5 5 2.5 3.5 3 2 4 1.5z"/>
        </svg>
        <span>612 408 3917</span>
      </li>
      <li class="contact-item">
        <svg class="contact-icon" viewBox="0 0 20 20" aria-hidden="true">
          <rect x="1" y="4" width="18" height="12" fill="#f3e01a"/>
          <path d="M1.5 4.5L10 11l8.5-6.5" fill="none" stroke="#000" stroke-width="1.4"/>
        </svg>
        <span>curtis@ridgelinejourneys.com</span>
      </li>
      <li class="contact-item">
        <svg class="contact-icon" viewBox="0 0 20 20" aria-hidden="true">
          <circle cx="10" cy="10" r="8.5" fill="#f3e01a"/>
          <path d="M6 5c2 0 3 1.5 2.5 3S6 9 5.5 11 7 14 8 16M12 4c0 2 2 2 3 3.5s-1 3-2 4-.5 3 .5 4" fill="none" stroke="#000" stroke-width="1.6"/>
        </svg>
        <span>www.ridgelinejourneys.com.au</span>
      </li>
    </ul>

    <div class="tagline">Adventure Riding GPS trails</div>
  </div>
</body>
</html>
```